Flat Belly Design Graphics for Social

I want to create 9 social media graphics (new Instagram size 4:5 (1080 x 1350 pixels) focusing on our Flat Belly Graphics, using the pics attached. Use the attached pics, NO RANDOM STOCK PHOTOGRAPHY. For the color scheme of the graphics, the color palette is attached. YOU MUST POST ALL 9 GRAPHICS IN ONE ENTRY.
Using the 3 titles below, create one set of graphics. 1) with all text, then for the others, use the pictures as detailed below in IMPORTANT:
1. Ten-Week Bright Morning Reboot
2. The Quick Garden Kitchen Menu Guide
3. Studio Habits for Lasting Energy Past Midlife - Zero Gym Needed
IMPORTANT:
Only use RK Pic 1 and RK Pic 2 with the title, Ten-Week Bright Morning Reboot
Only use meal plan1 and meal plan2 pics with the title, Quick Garden Kitchen Menu Guide
Only use studio habits 1 and studio habits 2 pics with the title, Studio Habits for Lasting Energy Past Midlife - Zero Gym Needed
women over 40

```html
<!DOCTYPE html>
<html lang="en">
<head>
<meta charset="utf-8">
<title>Bright Morning Social Set</title>
<link href="https://fonts.googleapis.com/css2?family=Oswald:wght@300;500;700&display=swap" rel="stylesheet">
<style>
  :root {
    --canvas: #1b0309;
    --blush: #faeded;
    --pink: #e29ab0;
    --pink-soft: #f6d5df;
    --green: #2f4e48;
    --green-top: #3f8a80;
    --green-bottom: #2b4944;
    --white: #ffffff;
  }
  * { margin: 0; padding: 0; box-sizing: border-box; }
  html, body { width: 1074px; height: 1200px; overflow: hidden; background: var(--canvas); }
  body { position: relative; font-family: "Oswald", "Arial Narrow", sans-serif; }
  .defs { position: absolute; width: 0; height: 0; }
  .tile {
    position: absolute; width: 259px; height: 324px;
    background: var(--blush); overflow: hidden;
  }
  .tile > svg { position: absolute; inset: 0; width: 259px; height: 324px; }
  .col-1 { left: 122px; } .col-2 { left: 405px; } .col-3 { left: 684px; }
  .row-1 { top: 94px; } .row-2 { top: 438px; } .row-3 { top: 782px; }
  .copy { position: absolute; line-height: 1; }
  .copy span { display: block; white-space: nowrap; }
  .center { left: 0; right: 0; text-align: center; }
  .white { color: var(--white); }
  .pink { color: var(--pink); }
  .bold { font-weight: 700; }
  .medium { font-weight: 500; }
  .light { font-weight: 300; }
  .copy .pill {
    display: inline-block; background: var(--green); color: var(--white);
    border-radius: 50%; padding: 5px 18px 7px; font-weight: 500;
  }
  .copy .inline { display: inline; }
  .caps { text-transform: uppercase; letter-spacing: -0.5px; }
</style>
</head>
<body>

<svg class="defs" aria-hidden="true">
  <defs>
    <linearGradient id="greenFade" x1="0" y1="0" x2="0" y2="1">
      <stop offset="0" stop-color="#3f8a80"/>
      <stop offset="1" stop-color="#2b4944"/>
    </linearGradient>
    <linearGradient id="portraitTone" x1="0" y1="0" x2="0" y2="1">
      <stop offset="0" stop-color="#c99a82"/>
      <stop offset="0.55" stop-color="#eee7e4"/>
      <stop offset="1" stop-color="#3a2a2a"/>
    </linearGradient>
    <linearGradient id="foodTone" x1="0" y1="0" x2="1" y2="1">
      <stop offset="0" stop-color="#6b8a3a"/>
      <stop offset="0.5" stop-color="#b4452f"/>
      <stop offset="1" stop-color="#4a3424"/>
    </linearGradient>
    <linearGradient id="friendsTone" x1="0" y1="0" x2="0" y2="1">
      <stop offset="0" stop-color="#4b3428"/>
      <stop offset="0.5" stop-color="#d9a88f"/>
      <stop offset="1" stop-color="#9fb6cc"/>
    </linearGradient>
  </defs>
</svg>

<!-- Row 1 : text only -->
<section class="tile col-1 row-1">
  <svg viewBox="0 0 259 324" aria-hidden="true">
    <polygon points="200,30 280,80 280,250 200,298 120,250 120,80" fill="var(--green)" stroke="var(--green)" stroke-width="24" stroke-linejoin="round"/>
    <polygon points="129,28 230,86 230,236 129,292 28,236 28,86" fill="var(--pink)" stroke="var(--pink)" stroke-width="24" stroke-linejoin="round"/>
  </svg>
  <div class="copy center" style="top:52px">
    <span><span class="pill" style="font-size:24px">Ten-Week</span></span>
    <span class="white bold caps" style="font-size:64px;margin-top:4px">BRIGHT</span>
    <span class="white bold caps" style="font-size:42px">MORNING</span>
    <span class="white medium" style="font-size:32px;margin-top:4px">Reboot</span>
  </div>
</section>

<section class="tile col-2 row-1">
  <svg viewBox="0 0 259 324" aria-hidden="true">
    <polygon points="60,30 140,80 140,250 60,298 -20,250 -20,80" fill="var(--pink)" stroke="var(--pink)" stroke-width="24" stroke-linejoin="round"/>
    <polygon points="129,28 230,86 230,236 129,292 28,236 28,86" fill="var(--green)" stroke="var(--green)" stroke-width="24" stroke-linejoin="round"/>
  </svg>
  <div class="copy center" style="top:56px">
    <span class="white light" style="font-size:28px">The Quick</span>
    <span class="white bold caps" style="font-size:52px;margin-top:4px">GARDEN</span>
    <span class="white bold caps" style="font-size:48px">KITCHEN</span>
    <span class="white light" style="font-size:32px;margin-top:6px">MENU GUIDE</span>
  </div>
</section>

<section class="tile col-3 row-1">
  <svg viewBox="0 0 259 324" aria-hidden="true">
    <polygon points="60,30 140,80 140,250 60,298 -20,250 -20,80" fill="var(--green)" stroke="var(--green)" stroke-width="24" stroke-linejoin="round"/>
    <polygon points="129,28 230,86 230,236 129,292 28,236 28,86" fill="var(--pink)" stroke="var(--pink)" stroke-width="24" stroke-linejoin="round"/>
  </svg>
  <div class="copy center" style="top:58px">
    <span><span class="pill" style="font-size:15px;padding:8px 22px 9px">Studio Habits for</span></span>
    <span class="white bold caps" style="font-size:56px;margin-top:8px">LASTING</span>
    <span class="white bold caps" style="font-size:56px">ENERGY</span>
    <span class="white medium" style="font-size:11.5px;margin-top:8px">Past Midlife - Zero Gym Needed</span>
  </div>
</section>

<!-- Row 2 -->
<section class="tile col-1 row-2">
  <svg viewBox="0 0 259 324">
    <path d="M71,0 H259 V120 L165,172 L71,120 Z" fill="var(--pink-soft)"/>
    <path d="M100,4 H236 V118 L168,164 L100,118 Z" fill="url(#portraitTone)" role="img" aria-label="Photo: smiling woman in a white cropped knit top, pointing at her waist"/>
    <polygon points="33,20 50,30 50,50 33,60 16,50 16,30" fill="var(--pink)" stroke="var(--pink)" stroke-width="8" stroke-linejoin="round"/>
    <polygon points="250,160 270,175 270,265 250,276 232,265 232,175" fill="var(--pink)" stroke="var(--pink)" stroke-width="16" stroke-linejoin="round"/>
    <polygon points="219,292 225,296 225,302 219,306 213,302 213,296" fill="var(--pink)"/>
    <circle cx="235" cy="316" r="2.5" fill="var(--pink)"/>
    <path d="M-10,196 L60,150 L200,226 V330 H-10 Z" fill="url(#greenFade)" stroke="url(#greenFade)" stroke-width="14" stroke-linejoin="round"/>
  </svg>
  <div class="copy" style="left:17px;top:192px">
    <span class="pink medium" style="font-size:21px">Ten-Week</span>
    <span class="white medium" style="font-size:27px;margin-top:5px">Bright Morning</span>
    <span class="pink medium" style="font-size:34px;margin-top:5px">Reboot</span>
  </div>
</section>

<section class="tile col-2 row-2">
  <svg viewBox="0 0 259 324">
    <path d="M-10,-10 H201 V116 L100,170 L-10,112 Z" fill="url(#greenFade)" stroke="url(#greenFade)" stroke-width="14" stroke-linejoin="round"/>
    <polygon points="228,16 244,26 244,44 228,54 212,44 212,26" fill="var(--pink)" stroke="var(--pink)" stroke-width="8" stroke-linejoin="round"/>
    <polygon points="225,126 232,130 232,137 225,141 218,137 218,130" fill="var(--pink)"/>
    <circle cx="241" cy="149" r="2.5" fill="var(--pink)"/>
    <polygon points="10,158 50,180 50,238 10,258 -30,238 -30,180" fill="var(--pink)" stroke="var(--pink)" stroke-width="16" stroke-linejoin="round"/>
    <polygon points="45,270 60,279 60,297 45,306 30,297 30,279" fill="var(--pink)" stroke="var(--pink)" stroke-width="8" stroke-linejoin="round"/>
    <path d="M170,146 L262,190 V330 H88 V196 Z" fill="url(#foodTone)" stroke="url(#foodTone)" stroke-width="16" stroke-linejoin="round" role="img" aria-label="Photo: meal plan sheet surrounded by fresh fruit, chicken, asparagus and chickpeas"/>
  </svg>
  <div class="copy" style="left:20px;top:18px">
    <span class="pink medium" style="font-size:22px">The Quick</span>
    <span class="white bold" style="font-size:25px;margin-top:5px;letter-spacing:-0.3px">GARDEN KITCHEN</span>
    <span class="pink medium" style="font-size:34px;margin-top:5px">Menu Guide</span>
  </div>
</section>

<section class="tile col-3 row-2">
  <svg viewBox="0 0 259 324">
    <path d="M71,0 H259 V120 L165,172 L71,120 Z" fill="url(#friendsTone)" stroke="url(#friendsTone)" stroke-width="14" stroke-linejoin="round" role="img" aria-label="Photo: one woman whispering a secret to a surprised friend"/>
    <polygon points="33,20 50,30 50,50 33,60 16,50 16,30" fill="var(--pink)" stroke="var(--pink)" stroke-width="8" stroke-linejoin="round"/>
    <polygon points="250,160 270,175 270,265 250,276 232,265 232,175" fill="var(--pink)" stroke="var(--pink)" stroke-width="16" stroke-linejoin="round"/>
    <polygon points="219,292 225,296 225,302 219,306 213,302 213,296" fill="var(--pink)"/>
    <circle cx="235" cy="316" r="2.5" fill="var(--pink)"/>
    <path d="M-10,196 L79,152 L200,222 V330 H-10 Z" fill="url(#greenFade)" stroke="url(#greenFade)" stroke-width="14" stroke-linejoin="round"/>
  </svg>
  <div class="copy" style="left:18px;top:195px">
    <span class="pink medium" style="font-size:18px">Studio Habits for</span>
    <span class="white medium" style="font-size:28px;margin-top:5px">Lasting Energy</span>
    <span class="white medium" style="font-size:17px;margin-top:6px;line-height:1.25">Past Midlife - Zero Gym</span>
    <span class="white medium" style="font-size:17px;line-height:1.25">Needed</span>
  </div>
</section>

<!-- Row 3 -->
<section class="tile col-1 row-3">
  <svg viewBox="0 0 259 324">
    <path d="M37,-10 H223 V125 L130,172 L37,125 Z" fill="url(#portraitTone)" stroke="url(#portraitTone)" stroke-width="12" stroke-linejoin="round" role="img" aria-label="Photo: smiling woman in a kitchen wearing a white cropped knit top, pointing at her waist"/>
    <polygon points="36,12 54,22 54,42 36,52 18,42 18,22" fill="var(--pink)" stroke="var(--pink)" stroke-width="10" stroke-linejoin="round"/>
    <polygon points="220,164 227,168 227,176 220,180 213,176 213,168" fill="var(--pink)"/>
    <circle cx="238" cy="186" r="2.5" fill="var(--pink)"/>
    <path d="M130,170 L234,212 V330 H25 V212 Z" fill="url(#greenFade)" stroke="url(#greenFade)" stroke-width="14" stroke-linejoin="round"/>
  </svg>
  <div class="copy center" style="top:195px">
    <span class="pink medium" style="font-size:22px">Ten-Week</span>
    <span class="white medium" style="font-size:31px;margin-top:5px">Bright Morning</span>
    <span class="pink medium" style="font-size:34px;margin-top:5px">Reboot</span>
  </div>
</section>

<section class="tile col-2 row-3">
  <svg viewBox="0 0 259 324">
    <polygon points="25,10 41,20 41,40 25,50 9,40 9,20" fill="var(--pink)" stroke="var(--pink)" stroke-width="8" stroke-linejoin="round"/>
    <polygon points="61,22 67,26 67,32 61,36 55,32 55,26" fill="var(--pink)"/>
    <polygon points="250,160 270,175 270,265 250,276 232,265 232,175" fill="var(--pink)" stroke="var(--pink)" stroke-width="16" stroke-linejoin="round"/>
    <polygon points="160,282 168,287 168,296 160,301 152,296 152,287" fill="var(--pink)"/>
    <polygon points="201,282 214,290 214,306 201,314 188,306 188,290" fill="var(--pink)" stroke="var(--pink)" stroke-width="8" stroke-linejoin="round"/>
    <path d="M-10,90 H170 L205,175 L140,282 H-10 Z" fill="url(#greenFade)" stroke="url(#greenFade)" stroke-width="16" stroke-linejoin="round"/>
    <path d="M192,12 L262,44 V148 L192,178 L126,146 V46 Z" fill="url(#foodTone)" stroke="url(#foodTone)" stroke-width="14" stroke-linejoin="round" role="img" aria-label="Photo: salmon, avocado, tomatoes, eggs and lentils around a meal plan notebook"/>
  </svg>
  <div class="copy" style="left:12px;top:160px">
    <span class="pink medium" style="font-size:22px">The Quick</span>
    <span class="white medium" style="font-size:27px;margin-top:5px">Garden Kitchen</span>
    <span class="pink medium" style="font-size:32px;margin-top:5px">Menu Guide</span>
  </div>
</section>

<section class="tile col-3 row-3">
  <svg viewBox="0 0 259 324">
    <path d="M71,-10 H265 V192 L165,192 L71,150 Z" fill="url(#greenFade)" stroke="url(#greenFade)" stroke-width="12" stroke-linejoin="round"/>
    <polygon points="33,14 50,24 50,44 33,54 16,44 16,24" fill="var(--pink-soft)" stroke="var(--pink-soft)" stroke-width="8" stroke-linejoin="round"/>
    <polygon points="28,62 35,66 35,74 28,78 21,74 21,66" fill="var(--pink-soft)"/>
    <circle cx="28" cy="88" r="2.5" fill="var(--pink-soft)"/>
    <polygon points="250,164 270,176 270,206 250,218 236,206 236,176" fill="var(--pink)" stroke="var(--pink)" stroke-width="10" stroke-linejoin="round"/>
    <polygon points="218,284 225,288 225,296 218,300 211,296 211,288" fill="var(--pink)"/>
    <circle cx="235" cy="306" r="2.5" fill="var(--pink)"/>
    <path d="M101,136 L198,182 V330 H4 V182 Z" fill="var(--pink)" stroke="var(--pink)" stroke-width="14" stroke-linejoin="round"/>
    <path d="M30,172 H168 V324 H30 Z" fill="url(#friendsTone)" role="img" aria-label="Photo: two women sharing a secret, one whispering and one delighted"/>
  </svg>
  <div class="copy" style="right:14px;top:30px;text-align:right">
    <span class="pink medium" style="font-size:18px">Studio Habits for</span>
    <span class="white medium" style="font-size:27px;margin-top:5px">Lasting Energy</span>
    <span class="white medium" style="font-size:17px;margin-top:6px;line-height:1.25">Past Midlife - <span class="pink inline">Zero Gym</span></span>
    <span class="pink medium" style="font-size:17px;line-height:1.25">Needed</span>
  </div>
</section>

</body>
</html>
```